VOMRA Pty Ltd Business Card

Looking for a simple yet eye-catching double-sided business card design using my company logo on one side and contact details on the other.

Target Market(s)

Government

Industry/Entity Type

Communication Systems Engineering

Contact Information for Business Card

VOMRA Pty Ltd

Requirements
Nice to have
• Would be great to have a QR code so details can be scanned into contacts

```html
<!DOCTYPE html>
<html lang="en">
<head>
<meta charset="utf-8">
<title>VOMRA Pty Ltd Business Card</title>
<link rel="stylesheet" href="https://fonts.googleapis.com/css2?family=Open+Sans:wght@400;600;700;800&display=swap">
<style>
  :root {
    --slate: #353f46;
    --paper: #ffffff;
    --backdrop: #e9e7e3;
    --ink: #1f2326;
    --rule: #3a444b;
  }
  * { box-sizing: border-box; margin: 0; padding: 0; }
  html, body { width: 1200px; height: 780px; overflow: hidden; }
  body {
    background: var(--backdrop);
    font-family: "Open Sans", Arial, sans-serif;
    color: var(--ink);
    display: flex;
    align-items: center;
    justify-content: center;
    gap: 40px;
  }
  .card {
    position: relative;
    width: 540px;
    height: 310px;
    background: var(--paper);
    overflow: hidden;
    box-shadow: 0 10px 26px rgba(0,0,0,0.16);
  }
  .card__band { position: absolute; inset: 0; width: 100%; height: 100%; }

  /* Front */
  .brand {
    position: absolute;
    left: 150px; top: 40px;
    display: flex; align-items: center; gap: 14px;
  }
  .brand__mark { width: 22px; height: 22px; background: var(--slate); }
  .brand__name {
    font-weight: 800; font-size: 50px; letter-spacing: 4px;
    color: var(--slate); line-height: 1;
  }
  .front__rule {
    position: absolute; left: 32px; top: 128px;
    width: 330px; height: 1.5px; background: var(--rule);
  }
  .person { position: absolute; right: 44px; top: 142px; text-align: right; }
  .person__name { font-weight: 700; font-size: 30px; color: var(--slate); line-height: 1.1; }
  .person__role { font-size: 15px; margin-top: 2px; }
  .contacts { position: absolute; left: 30px; top: 150px; list-style: none; }
  .contacts li {
    display: flex; align-items: center; gap: 7px;
    font-size: 12.5px; line-height: 19px;
  }
  .contacts svg { width: 11px; height: 11px; fill: var(--slate); flex: none; }
  .address {
    position: absolute; left: 200px; bottom: 36px;
    font-size: 14px; line-height: 19px;
  }

  /* Back */
  .back__brand {
    position: absolute; right: 70px; top: 92px;
    display: flex; align-items: center; gap: 14px;
  }
  .back__brand .brand__name { font-size: 58px; }
  .back__brand .brand__mark { width: 26px; height: 26px; }
  .back__url {
    position: absolute; left: 118px; bottom: 12px;
    color: var(--paper); font-size: 14px; letter-spacing: 0.5px;
  }
</style>
</head>
<body>

<section class="card card--front" aria-label="Card front">
  <svg class="card__band" viewBox="0 0 540 310" preserveAspectRatio="none" aria-hidden="true">
    <polygon fill="var(--slate)" points="0,300 150,300 158,292 540,292 540,310 0,310"/>
    <polygon fill="var(--slate)" points="480,268 540,268 540,292 470,292"/>
  </svg>

  <div class="brand">
    <span class="brand__mark"></span>
    <span class="brand__name">VOMRA</span>
  </div>

  <div class="front__rule"></div>

  <ul class="contacts">
    <li>
      <svg viewBox="0 0 24 24"><path d="M6.6 10.8a15.1 15.1 0 0 0 6.6 6.6l2.2-2.2c.3-.3.7-.4 1-.2 1.1.4 2.3.6 3.6.6.6 0 1 .4 1 1V20c0 .6-.4 1-1 1A17 17 0 0 1 3 4c0-.6.4-1 1-1h3.5c.6 0 1 .4 1 1 0 1.3.2 2.5.6 3.6.1.3 0 .7-.2 1z"/></svg>
      (555) 214-3086
    </li>
    <li>
      <svg viewBox="0 0 24 24"><path d="M12 2a10 10 0 1 0 0 20 10 10 0 0 0 0-20zm6.9 6h-3a15.6 15.6 0 0 0-1.3-3.9A8 8 0 0 1 18.9 8zM12 4c.8 1.2 1.5 2.5 1.9 4h-3.8c.4-1.5 1.1-2.8 1.9-4zM4.3 14a8.2 8.2 0 0 1 0-4h3.4a16 16 0 0 0 0 4zm.8 2h3a15.6 15.6 0 0 0 1.3 3.9A8 8 0 0 1 5.1 16zm3-8h-3a8 8 0 0 1 4.3-3.9A15.6 15.6 0 0 0 8.1 8zM12 20c-.8-1.2-1.5-2.5-1.9-4h3.8c-.4 1.5-1.1 2.8-1.9 4zm2.3-6H9.7a14.7 14.7 0 0 1 0-4h4.6a14.7 14.7 0 0 1 0 4zm.3 5.9c.6-1.2 1-2.5 1.3-3.9h3a8 8 0 0 1-4.3 3.9zm1.7-5.9a16 16 0 0 0 0-4h3.4a8.2 8.2 0 0 1 0 4z"/></svg>
      www.vomra.com.au
    </li>
    <li>
      <svg viewBox="0 0 24 24"><path d="M3 5h18c.6 0 1 .4 1 1v12c0 .6-.4 1-1 1H3c-.6 0-1-.4-1-1V6c0-.6.4-1 1-1zm1 2.4V17h16V7.4l-8 5.3z"/></svg>
      admin@vomra.com.au
    </li>
  </ul>

  <div class="person">
    <p class="person__name">Sam Whitfield</p>
    <p class="person__role">Co-Founder</p>
  </div>

  <p class="address">27-29 Marlow Street Eastbrook<br>NSW 2190 Australia</p>
</section>

<section class="card card--back" aria-label="Card back">
  <svg class="card__band" viewBox="0 0 540 310" preserveAspectRatio="none" aria-hidden="true">
    <polygon fill="var(--slate)" points="0,296 105,296 112,282 540,282 540,310 0,310"/>
    <polygon fill="var(--slate)" points="105,296 112,270 200,266 540,266 540,282 112,282"/>
  </svg>

  <div class="back__brand">
    <span class="brand__mark"></span>
    <span class="brand__name">VOMRA</span>
  </div>

  <p class="back__url">www.vomra.com.au</p>
</section>

</body>
</html>
```